Residential Remodeling Contractor needs updated business card

I need a new design for my business card.
Name of the company is Ridgefell Construction. I need a card that commands presence, strength, integrity. I have been in business for 28 years. I am a Residential Remodeling Contractor that covers all aspects of a residential remodel and build.

```html
<!DOCTYPE html>
<html lang="en">
<head>
<meta charset="utf-8">
<title>Ridgefell Construction – Business Card</title>
<link href="https://fonts.googleapis.com/css2?family=Cinzel:wght@700&family=Open+Sans:wght@400&display=swap" rel="stylesheet">
<style>
  :root {
    --backdrop: #2a2a2b;
    --brand-blue: #1b3f7e;
    --card-white: #ffffff;
    --text-grey: #3a3a3a;
    --rule-blue: #2c4f92;
  }
  * { margin: 0; padding: 0; box-sizing: border-box; }
  html, body {
    width: 1200px; height: 878px; overflow: hidden;
    background: var(--backdrop);
  }
  .canvas {
    width: 1200px; height: 878px;
    display: flex; flex-direction: column;
    align-items: center; justify-content: center; gap: 40px;
  }
  .card {
    width: 630px; height: 360px; position: relative;
    box-shadow: 0 10px 28px rgba(0,0,0,.45);
  }
  /* Front side */
  .card--front {
    background: var(--brand-blue);
    display: flex; align-items: center; justify-content: center;
  }
  .wordmark {
    display: flex; align-items: center; gap: 18px;
    font-family: 'Cinzel', 'Times New Roman', serif; font-weight: 700;
    line-height: 1.05;
  }
  .wordmark__mark { width: 22px; height: 22px; }
  .wordmark__name { font-size: 44px; letter-spacing: 1px; }
  .wordmark__name span { display: block; }
  .wordmark__name span + span { font-size: 32px; letter-spacing: 2px; }
  .card--front .wordmark { color: var(--card-white); }
  .card--front .wordmark__mark { background: var(--card-white); }

  /* Back side */
  .card--back { background: var(--card-white); }
  .card--back .wordmark {
    position: absolute; top: 42px; left: 0; right: 0; justify-content: center;
    color: var(--brand-blue);
  }
  .card--back .wordmark__mark { background: var(--brand-blue); width: 18px; height: 18px; }
  .card--back .wordmark__name { font-size: 36px; }
  .card--back .wordmark__name span + span { font-size: 26px; }
  .person {
    position: absolute; top: 172px; left: 0; right: 0; text-align: center;
  }
  .person__name {
    font-family: 'Cinzel', 'Times New Roman', serif; font-weight: 700;
    font-size: 24px; color: var(--brand-blue); letter-spacing: 1px;
  }
  .person__title {
    font-family: 'Open Sans', Arial, sans-serif; font-size: 13px;
    color: var(--text-grey); letter-spacing: .5px; margin-top: -2px;
  }
  .divider {
    position: absolute; top: 230px; left: 40px; right: 40px;
    height: 1px; background: var(--rule-blue);
  }
  .contacts {
    position: absolute; top: 244px; left: 40px; list-style: none;
    font-family: 'Open Sans', Arial, sans-serif; font-size: 13.5px; color: var(--text-grey);
  }
  .contacts li { display: flex; align-items: center; gap: 8px; height: 22px; }
  .contacts svg { width: 12px; height: 12px; fill: var(--brand-blue); }
  .address {
    position: absolute; right: 40px; bottom: 30px; text-align: right;
    font-family: 'Open Sans', Arial, sans-serif; font-size: 14px;
    color: var(--text-grey); line-height: 1.45; letter-spacing: .5px;
  }
</style>
</head>
<body>
<main class="canvas">
  <section class="card card--front" aria-label="Card front">
    <div class="wordmark">
      <span class="wordmark__mark"></span>
      <div class="wordmark__name"><span>Ridgefell</span><span>Construction</span></div>
    </div>
  </section>

  <section class="card card--back" aria-label="Card back">
    <div class="wordmark">
      <span class="wordmark__mark"></span>
      <div class="wordmark__name"><span>Ridgefell</span><span>Construction</span></div>
    </div>
    <div class="person">
      <div class="person__name">DANIEL WHITCOMBE</div>
      <div class="person__title">Owner &amp; Manager</div>
    </div>
    <div class="divider"></div>
    <ul class="contacts">
      <li>
        <svg viewBox="0 0 24 24" aria-hidden="true"><path d="M6.6 10.8a15 15 0 0 0 6.6 6.6l2.2-2.2a1 1 0 0 1 1-.25 11.4 11.4 0 0 0 3.6.6 1 1 0 0 1 1 1V20a1 1 0 0 1-1 1A17 17 0 0 1 3 4a1 1 0 0 1 1-1h3.5a1 1 0 0 1 1 1c0 1.25.2 2.45.6 3.6a1 1 0 0 1-.25 1z"/></svg>
        555 214 7730
      </li>
      <li>
        <svg viewBox="0 0 24 24" aria-hidden="true"><path d="M2 5h20v14H2zm2 2v.5l8 5 8-5V7z"/></svg>
        info@ridgefellbuild.com
      </li>
      <li>
        <svg viewBox="0 0 24 24" aria-hidden="true"><circle cx="12" cy="12" r="10"/></svg>
        www.ridgefellbuild.com
      </li>
    </ul>
    <div class="address">
      P.O. Box&nbsp; Street Name<br>
      Country Name AB, A5B 521
    </div>
  </section>
</main>
</body>
</html>
```